Gravelstern Rum Liqueur Bottle Label

I will be launching a Rum Liqueur called Gravelstern Spiced Rum Liqueur. The bottle I have chosen to use is an KVT 500ml type and I have included a photo of it in the project brief. The bottle dimensions are height 193.5mm with diameter 85mm. There will be a cork closure, sealed with a heat shrink capsule. I require two labels for each bottle, a large rectangular label on the front with the product name, logo, label design and the bottle quantity which is 500ml. The front label should also contain the strength of the liqueur which is 25% vol. The rear label will contain the required UK legal information such as government health warning, number of UK units of alcohol as well as the place of bottling which is Wick, Caithness, Scotland. A barcode will also be on the rear label and I have added it as a jpg file. On my current homemade label I also have the following text on the rear label: "Due to the ferocious tides, currents and winds that shape the narrow stretch of water separating Caithness from the Orkney Islands in the far North of Scotland, it has become known to generations of sailors as "Gravelstern" and is the graveyard of countless number of ships. Gravelstern Spiced Rum Liqueur aims to capture the spirit of those brave men and women who have risked all on these treacherous shores". For the main front label I am keen for the designer to explore the themes of shipwreck, sea monsters, smuggling, pistols, diving helmets, heavy seas, sea stacks, high cliffs, sealife etc. I have included a story about a local smuggler called Peter Mowbray as an example of an inspirational theme. I currently also have a website regarding Caithness shipwrecks which can be found at www.gravelstern.example and which could provide some further ideas. My feeling is that the label design should be masculine and I would like to keep away from designs that would make the label costly to print. I have included a file with my current logo but please feel free to change its colour as required and to remove the word Gravelstern from the logo if you wish. I can supply the logo file in different formats such as jpg, ai, eps, pdf, png or psd. I also have the barcode in pdf, png or svg formats. The word Gravelstern is a registered trademark.I have also attached a photograph of my liqueur in an attempt to show the colour of the finished product and the bottle style.
Updates
Colors
Designer to choose colors to be used in the design.
Look and feel
Each slider illustrates characteristics of the customer's brand and the style your logo design should communicate.

```html
<!DOCTYPE html>
<html lang="en">
<head>
<meta charset="utf-8">
<title>Gravelstern Spiced Rum Liqueur – Label</title>
<link rel="stylesheet" href="https://fonts.googleapis.com/css2?family=Germania+One&family=Open+Sans:wght@300;400&display=swap">
<style>
  :root {
    --page: #ffffff;
    --label-paper: #e9e5dc;
    --label-paper-edge: #dbd6ca;
    --label-rim: #4a403b;
    --ink: #2f2926;
    --ribbon-cream: #efebe3;
    --ribbon-gold: #e2c27a;
    --art-light: #d6d1c7;
    --art-dark: #bbb4a7;
    --badge: #4a403b;
    --badge-text: #f4f1ec;
  }
  html, body {
    margin: 0;
    padding: 0;
    width: 1200px;
    height: 2835px;
    overflow: hidden;
    background: var(--page);
  }
  .label-sheet {
    position: relative;
    width: 1200px;
    height: 2835px;
  }
  .label-art {
    position: absolute;
    inset: 0;
  }
  .brand-title {
    font-family: "Germania One", "Pirata One", serif;
    fill: var(--ink);
  }
  .brand-subtitle {
    font-family: "Germania One", "Pirata One", serif;
    fill: var(--ink);
  }
  .volume-badge {
    position: absolute;
    left: 36px;
    top: 1846px;
    width: 212px;
    height: 212px;
    border-radius: 50%;
    background: var(--badge);
    color: var(--badge-text);
    display: flex;
    flex-direction: column;
    align-items: center;
    justify-content: center;
    font-family: "Open Sans", Arial, sans-serif;
    line-height: 1.15;
  }
  .volume-badge .volume { font-size: 48px; font-weight: 400; }
  .volume-badge .strength { font-size: 38px; font-weight: 300; }
</style>
</head>
<body>
<main class="label-sheet">
  <svg class="label-art" width="1200" height="2835" viewBox="0 0 1200 2835" xmlns="http://www.w3.org/2000/svg">
    <defs>
      <radialGradient id="paperTone" cx="50%" cy="45%" r="60%">
        <stop offset="0%" stop-color="var(--label-paper)"/>
        <stop offset="100%" stop-color="var(--label-paper-edge)"/>
      </radialGradient>
      <linearGradient id="artTone" x1="0" y1="0" x2="1" y2="1">
        <stop offset="0%" stop-color="var(--art-light)"/>
        <stop offset="100%" stop-color="var(--art-dark)"/>
      </linearGradient>
    </defs>

    <g class="round-label" transform="translate(600 1337) scale(1.28)">
      <!-- Label disc -->
      <circle class="label-disc" cx="0" cy="0" r="438" fill="url(#paperTone)" stroke="var(--label-rim)" stroke-width="10"/>

      <!-- Illustration area -->
      <rect class="label-illustration" x="-250" y="-320" width="500" height="370" rx="40"
            fill="url(#artTone)" role="img"
            aria-label="Engraved illustration of a rum barrel, a brass diving helmet, an anchor with rope, a spyglass and a seagull"/>

      <!-- Gold ribbon tail -->
      <path class="ribbon-gold" d="M-230,250 Q0,285 230,250 L215,335 Q0,370 -215,335 Z"
            fill="var(--ribbon-gold)" stroke="var(--ink)" stroke-width="2.5"/>

      <!-- Name ribbon -->
      <path class="ribbon-name" d="M-325,45 Q0,20 325,45 L298,100 L325,160 Q0,135 -325,160 L-298,100 Z"
            fill="var(--ribbon-cream)" stroke="var(--ink)" stroke-width="3"/>
      <text class="brand-title" x="0" y="135" text-anchor="middle" font-size="96" textLength="500" lengthAdjust="spacingAndGlyphs">GRAVELSTERN</text>

      <!-- Subtitle ribbon -->
      <path class="ribbon-subtitle" d="M-275,175 Q0,195 275,175 L275,258 Q0,278 -275,258 Z"
            fill="var(--ribbon-cream)" stroke="var(--ink)" stroke-width="3"/>
      <text class="brand-subtitle" x="0" y="244" text-anchor="middle" font-size="58" textLength="470" lengthAdjust="spacingAndGlyphs">SPICED RUM LIQUEUR</text>
    </g>
  </svg>

  <div class="volume-badge">
    <span class="volume">500ml.</span>
    <span class="strength">25% vol.</span>
  </div>
</main>
</body>
</html>
```